gift box for organic and natural food items

My brand name is Tiller's Pantry and we are selling organic dried food to Korea now. We focus on transparent from the family farm to the customer directly with the single or simple organic ingredient. Our main customers are mainly woman from 30 to 50 years old. We have 4 different products for this package. Organic dried cherry, Organic dried figs, Organic dried dates and Organic dried pistachio. I would like to make a gift box that woman want to have and hold our natural products. The material of the gift box will be Royal Ivory Paper.

Target Market(s)

We will sell these items and gift box at the luxury department store.

Industry/Entity Type

Food Production

Font styles to use
Serif
Script

Colors
9ccb3b

Requirements
Must have
• Our slogan: A gift from the farm brought fresh to your door
• Our producer image: I will upload our producer's image
• We focus on the transparent and our producers.
• I will provide you with the image file for the only producers later.
Nice to have
• Brand logo / Our brand introduction sentences / NFCB logo / Color
• Color : Green & Bright Beige
• "Indulge. Nourish. Enjoy"
• "Taste the difference.
• The difference is quality.
• Quality you can experience"
• "As you savor the farm fresh delicacies enclosed in every box, relish in the fact that each ingredient was meticulously selected and directly sourced from hard working family farms. The result is a snacking experience like none other. With quality you can taste, our organic treats boast a unique flavor that will tantalize the taste buds. "
• "Upgrade your nourishment.
• Upgrade your nutrition.
• Upgrade your snack."
Should not have
• Too complicated with many colors

```html
<!DOCTYPE html>
<html lang="en">
<head>
<meta charset="utf-8">
<title>Tiller's Pantry — Gift Box Dieline</title>
<link href="https://fonts.googleapis.com/css2?family=Didact+Gothic&family=Nanum+Gothic&display=swap" rel="stylesheet">
<style>
  :root {
    --paper: #ffffff;
    --kraft: #e3c8a8;
    --kraft-light: #e8d6bb;
    --green: #5cb874;
    --green-deep: #2e9a57;
    --lime: #d4df2a;
    --cut: #e5394a;
    --fold: #7a6ab0;
    --spec-frame: #b0449a;
    --ink: #333333;
    --portrait: #9a9a98;
    --portrait-color: #7f8ea8;
  }
  html, body { margin: 0; padding: 0; width: 1200px; height: 770px; overflow: hidden; background: var(--paper); }
  .dieline { display: block; width: 1200px; height: 770px; }
  .cut { stroke: var(--cut); stroke-width: 1; }
  .fold { stroke: var(--fold); stroke-width: 0.8; fill: none; }
  .panel-kraft { fill: var(--kraft); }
  .panel-light { fill: var(--kraft-light); }
  .hole { fill: var(--paper); }
  .base-band { fill: var(--green); }
  .spec-text { font-family: "Nanum Gothic", sans-serif; font-size: 10px; fill: var(--ink); }
  .brand-name { font-family: "Didact Gothic", sans-serif; fill: var(--green-deep); }
  .slogan-bar { fill: var(--green); }
  .slogan-text { font-family: "Didact Gothic", sans-serif; font-size: 7.6px; fill: #ffffff; }
  .quote { font-family: "Didact Gothic", sans-serif; font-size: 11.5px; fill: var(--green); letter-spacing: 0.6px; }
  .badge { fill: #ffffff; stroke: var(--green-deep); stroke-width: 3; }
</style>
</head>
<body>
<svg class="dieline" viewBox="0 0 1500 962" xmlns="http://www.w3.org/2000/svg">
  <defs>
    <radialGradient id="splash-left" cx="1" cy="0.45" r="1">
      <stop offset="0" stop-color="#d4df2a"/>
      <stop offset="0.35" stop-color="#9ccb3b"/>
      <stop offset="0.7" stop-color="#5cb874"/>
      <stop offset="1" stop-color="#5cb874" stop-opacity="0"/>
    </radialGradient>
    <radialGradient id="splash-right" cx="0" cy="0.45" r="1">
      <stop offset="0" stop-color="#d4df2a"/>
      <stop offset="0.35" stop-color="#9ccb3b"/>
      <stop offset="0.7" stop-color="#5cb874"/>
      <stop offset="1" stop-color="#5cb874" stop-opacity="0"/>
    </radialGradient>
    <linearGradient id="portrait-sketch" x1="0" y1="0" x2="0" y2="1">
      <stop offset="0" stop-color="#c9c6c0"/>
      <stop offset="1" stop-color="#8e8d8a"/>
    </linearGradient>
    <linearGradient id="portrait-photo" x1="0" y1="0" x2="0" y2="1">
      <stop offset="0" stop-color="#b9b3a8"/>
      <stop offset="1" stop-color="#5d6f95"/>
    </linearGradient>
  </defs>

  <!-- spec label -->
  <g class="spec-label">
    <rect x="244" y="63" width="205" height="133" fill="none" stroke="var(--spec-frame)" stroke-width="1"/>
    <rect x="248" y="67" width="197" height="125" fill="none" stroke="var(--spec-frame)" stroke-width="0.8"/>
    <text class="spec-text" x="263" y="101">업체: 틸러스팬트리</text>
    <text class="spec-text" x="263" y="117">품명: 체리5입,피스타치오2입 공용</text>
    <text class="spec-text" x="263" y="133">재질: 무광 RIV 350</text>
    <text class="spec-text" x="263" y="149">특이사항:</text>
    <text class="spec-text" x="263" y="165">작업일: 19.07.26</text>
  </g>

  <!-- glue flap -->
  <path class="panel-kraft cut" d="M141 249 L108 258 L108 690 Q110 708 122 710 L141 710 Z"/>

  <!-- front panel -->
  <g class="front-panel">
    <rect class="panel-kraft" x="141" y="249" width="412" height="461"/>
    <rect x="415" y="255" width="138" height="447" fill="url(#splash-left)" role="img" aria-label="Green and lime brush splash decoration"/>
    <rect class="hole cut" x="271" y="283" width="152" height="47" rx="23"/>
    <rect class="hole cut" x="313" y="349" width="67" height="5" rx="2.5"/>
    <text class="brand-name" x="206" y="414" font-size="42">Tiller's</text>
    <text class="brand-name" x="212" y="443" font-size="18" letter-spacing="9">PANTRY</text>
    <rect class="slogan-bar" x="205" y="451" width="178" height="12"/>
    <text class="slogan-text" x="209" y="460">A gift from the farm brought fresh to your door</text>
    <text class="quote" x="205" y="483">"Taste the difference.</text>
    <text class="quote" x="205" y="501">The difference is quality.</text>
    <text class="quote" x="205" y="519">Quality you can experience"</text>
    <rect x="147" y="578" width="343" height="124" fill="url(#portrait-sketch)" role="img" aria-label="Pencil-sketch portraits of the four producers"/>
    <circle class="badge" cx="511" cy="688" r="19"/>
    <rect class="base-band" x="141" y="702" width="412" height="8"/>
  </g>

  <!-- side panels (right of front) -->
  <path class="panel-kraft cut" d="M553 249 L660 258 L660 710 L553 710 Z"/>
  <path class="panel-kraft cut" d="M660 258 L766 249 L766 710 L660 710 Z"/>
  <path class="fold" d="M553 710 L660 604 L766 710 M660 258 L660 604"/>
  <path class="panel-kraft cut" d="M555 712 L766 712 L660 818 L593 818 L555 742 Z"/>

  <!-- back panel -->
  <g class="back-panel">
    <path class="panel-kraft cut" d="M768 240 L768 130 Q770 103 800 103 L1140 103 Q1176 103 1176 130 L1178 240 Z"/>
    <path class="fold" d="M766 240 L1178 240 M766 248 L1178 248"/>
    <rect class="hole cut" x="900" y="160" width="146" height="41" rx="20"/>
    <path class="cut" fill="none" d="M935 133 Q950 130 972 148 Q994 130 1010 133"/>
    <circle cx="937" cy="133" r="2.5" fill="none" stroke="var(--cut)"/>
    <circle cx="1008" cy="133" r="2.5" fill="none" stroke="var(--cut)"/>
    <rect class="panel-light" x="766" y="249" width="412" height="461"/>
    <rect x="766" y="270" width="150" height="432" fill="url(#splash-right)" role="img" aria-label="Green and lime brush splash decoration"/>
    <rect class="hole cut" x="900" y="287" width="146" height="40" rx="20"/>
    <text class="brand-name" x="944" y="414" font-size="42">Tiller's</text>
    <text class="brand-name" x="950" y="443" font-size="18" letter-spacing="9">PANTRY</text>
    <rect class="slogan-bar" x="944" y="451" width="178" height="12"/>
    <text class="slogan-text" x="948" y="460">A gift from the farm brought fresh to your door</text>
    <text class="quote" x="944" y="483">"Taste the difference.</text>
    <text class="quote" x="944" y="501">The difference is quality.</text>
    <text class="quote" x="944" y="519">Quality you can experience"</text>
    <rect x="878" y="612" width="297" height="90" fill="url(#portrait-photo)" role="img" aria-label="Colour portraits of the four producers"/>
    <circle class="badge" cx="815" cy="688" r="19"/>
    <rect class="base-band" x="766" y="702" width="412" height="8"/>
  </g>

  <!-- side panels (right of back) -->
  <path class="panel-kraft cut" d="M1178 249 L1285 258 L1285 710 L1178 710 Z"/>
  <path class="panel-kraft cut" d="M1285 258 L1391 249 L1391 710 L1285 710 Z"/>
  <path class="fold" d="M1178 710 L1285 604 L1391 710 M1285 258 L1285 604"/>
  <path class="panel-kraft cut" d="M1180 712 L1391 712 L1285 818 L1220 818 L1180 762 Z"/>

  <!-- bottom flaps -->
  <path class="panel-kraft cut" d="M143 712 L548 712 L546 850 Q545 858 537 858 L478 858 L446 822 L350 822 L313 858 L160 858 Q150 858 150 848 Z"/>
  <path class="fold" d="M446 822 L548 722"/>
  <path class="panel-kraft cut" d="M768 712 L1176 712 L1170 850 Q1169 858 1161 858 L1110 858 L1073 822 L975 822 L937 858 L786 858 Q778 858 778 850 Z"/>
  <path class="fold" d="M1073 822 L1176 720"/>

  <!-- fold lines between panels -->
  <path class="fold" d="M141 249 L141 710 M553 249 L553 710 M766 249 L766 710 M1178 249 L1178 710 M141 710 L1391 710"/>
</svg>
</body>
</html>
```